Bubble map/flip book

I need someone to create a bubble map with explanations using the attached. This will be used to create a color coded flip book/manual. I need you to clean this up.

Marlowesintary@quillpost.net

```html
<!DOCTYPE html>
<html lang="en">
<head>
<meta charset="utf-8">
<title>Claim Denied for No Authorization / Referral</title>
<link rel="stylesheet" href="https://fonts.googleapis.com/css2?family=Arimo:wght@700&family=Open+Sans:ital,wght@0,700;1,400&display=swap">
<style>
  :root {
    --band-navy: #0a6699;
    --title-orange: #f5883a;
    --question-blue: #0199d9;
    --network-green: #9ac24a;
    --network-purple: #a86e98;
    --outcome-tan: #c89c52;
    --outcome-mauve: #a9919d;
    --footer-blue: #0a5a8c;
    --page-grey: #9a9a9a;
    --white: #ffffff;
  }
  * { box-sizing: border-box; margin: 0; padding: 0; }
  html, body { width: 927px; height: 1200px; overflow: hidden; background: var(--white); }
  .page {
    position: relative;
    width: 927px;
    height: 1200px;
    background: var(--white);
    font-family: "Open Sans", Arial, sans-serif;
    overflow: hidden;
  }
  .header-band {
    position: absolute; left: 0; top: 0;
    width: 927px; height: 328px;
    background: var(--band-navy);
  }
  .connectors { position: absolute; left: 0; top: 0; }
  .box {
    position: absolute;
    color: var(--white);
    font-weight: 700;
    border-radius: 12px;
    box-shadow: 10px 14px 22px rgba(0, 0, 0, 0.14);
  }
  .title-box {
    left: 78px; top: 74px; width: 756px; height: 144px;
    background: var(--title-orange);
    border: 4px solid var(--white);
    border-radius: 18px;
    box-shadow: 0 10px 18px rgba(0, 0, 0, 0.35);
    display: flex; align-items: center; justify-content: center;
    text-align: center;
    font-family: "Arimo", Arial, sans-serif;
    font-size: 51px;
    line-height: 48px;
    text-shadow: 2px 3px 4px rgba(0, 0, 0, 0.35);
  }
  .question-box {
    left: 80px; top: 258px; width: 753px; height: 112px;
    background: var(--question-blue);
    border-radius: 16px;
    box-shadow: 0 10px 16px rgba(0, 0, 0, 0.3);
    display: flex; align-items: center; justify-content: center;
    text-align: center;
    font-family: "Arimo", Arial, sans-serif;
    font-size: 25px;
    line-height: 30px;
    padding: 0 40px;
    text-shadow: 1px 2px 3px rgba(0, 0, 0, 0.35);
  }
  .branch-box {
    top: 472px; width: 254px; height: 253px;
    padding: 16px 18px;
    font-size: 19.5px;
    line-height: 23.8px;
  }
  .branch-in-network { left: 124px; background: var(--network-green); }
  .branch-out-network { left: 534px; background: var(--network-purple); }
  .branch-box p + p { margin-top: 23.8px; }
  .outcome-box {
    padding: 12px 15px;
    font-size: 16.5px;
    line-height: 20.3px;
    border-radius: 8px;
  }
  .outcome-denied { left: 77px; top: 821px; width: 166px; height: 166px; background: var(--outcome-tan); }
  .outcome-paid { left: 285px; top: 788px; width: 137px; height: 138px; background: var(--outcome-tan); padding: 20px 22px; }
  .outcome-review { left: 490px; top: 788px; width: 138px; height: 138px; background: var(--outcome-mauve); }
  .outcome-appeal { left: 666px; top: 821px; width: 167px; height: 166px; background: var(--outcome-mauve); }
  .site-url {
    position: absolute; right: 55px; top: 1142px;
    font-style: italic; font-weight: 400;
    font-size: 16px;
    color: var(--footer-blue);
  }
  .page-number {
    position: absolute; left: 894px; top: 1136px;
    width: 33px; height: 34px;
    background: var(--page-grey);
    color: var(--white);
    font-family: "Arimo", Arial, sans-serif;
    font-size: 24px;
    line-height: 34px;
    text-align: center;
    font-weight: 700;
  }
</style>
</head>
<body>
<div class="page">
  <div class="header-band"></div>

  <svg class="connectors" width="927" height="1200" viewBox="0 0 927 1200" aria-hidden="true">
    <line x1="251" y1="370" x2="251" y2="472" stroke="var(--network-green)" stroke-width="5"/>
    <line x1="661" y1="370" x2="661" y2="472" stroke="var(--network-purple)" stroke-width="5"/>
    <line x1="162" y1="725" x2="162" y2="821" stroke="var(--outcome-tan)" stroke-width="5"/>
    <line x1="354" y1="725" x2="354" y2="788" stroke="var(--outcome-tan)" stroke-width="5"/>
    <line x1="558" y1="725" x2="558" y2="788" stroke="var(--outcome-mauve)" stroke-width="5"/>
    <line x1="748" y1="725" x2="748" y2="821" stroke="var(--outcome-mauve)" stroke-width="5"/>
  </svg>

  <h1 class="box title-box">Claim denied for no<br>authorization / referral.</h1>

  <div class="box question-box">Contact carrier. Was claim processed in network or out of network.</div>

  <div class="box branch-box branch-in-network">
    <p>Claim has processed correctly as in network provider. Medical records printed and appeal sent for medical necessity.</p>
  </div>

  <div class="box branch-box branch-out-network">
    <p>Claim processed out of network. Contact with Carrier shows claim processed out of network in error.</p>
    <p>Will representative send the claim back for review?</p>
  </div>

  <div class="box outcome-box outcome-denied">Appeal denied as services were not emergent. Balance is patient responsibility.</div>
  <div class="box outcome-box outcome-paid">Appeal for claim paid.</div>
  <div class="box outcome-box outcome-review">Claim has been sent back for review. Follow up in 14 days.</div>
  <div class="box outcome-box outcome-appeal">Representative will not send the claim back for review. Appeal sent to carrier. Follow up 30 days.</div>

  <div class="site-url">www.claimsguidebook.net</div>
  <div class="page-number">2</div>
</div>
</body>
</html>
```